Local Flower Farm Needs Business Card Design

I need business cards designed for a flower farm based in Eudora, Kansas.
Business Info:
We are a local cut flower farm located in Eudora, Kansas, founded by Corinne Haldwick. What started as a passion for agriculture and search for more joy in daily life has blossomed into a small business dedicated to providing the community with beautiful, fresh, and sustainable flowers. We specialize in local, seasonal blooms, ensuring that every petal reflects the care and dedication we pour into our craft. Our mission is to deliver the highest quality flowers directly to our customers through local farmers markets and to florists who share our commitment to sustainability. Join us in celebrating the beauty of nature, one bloom at a time!
Contact Details:
Corinne Haldwick
Owner
Phone 913-555-0147
Facebook: Rosalind Thorpe Gardens
Instagram: @RosalindThorpeGardens
Website: RosalindThorpeGardens.example
Target Market(s)
Wholesale to Florists and Direct to Consumer via Farmers Market
Industry/Entity Type
Florist, Farm
Contact Information for Business Card
Name, Contact Info, Logo
Look and feel
Each slider illustrates characteristics of the customer's brand and the style your logo design should communicate.

```html
<!DOCTYPE html>
<html lang="en">
<head>
<meta charset="utf-8">
<title>Rosalind Thorpe Gardens – Business Card</title>
<link href="https://fonts.googleapis.com/css2?family=Libre+Baskerville:wght@400;700&family=Lato:wght@400&display=swap" rel="stylesheet">
<style>
  :root {
    --backdrop: #8e8e8e;
    --card-white: #ffffff;
    --deep-teal: #08262c;
    --ink-grey: #6f6f6f;
    --rule-grey: #7a7a7a;
  }
  * { box-sizing: border-box; margin: 0; padding: 0; }
  html, body { width: 1200px; height: 900px; overflow: hidden; }
  body {
    background: var(--backdrop);
    font-family: "Lato", sans-serif;
    position: relative;
  }
  .card {
    position: absolute;
    left: 280px;
    width: 640px;
    height: 366px;
    overflow: hidden;
    box-shadow: 0 10px 28px rgba(0,0,0,0.25);
  }
  .card--front { top: 60px; background: var(--card-white); }
  .card--back { top: 474px; background: var(--deep-teal); }

  .brand-seal {
    position: absolute;
    width: 200px; height: 200px;
    border-radius: 50%;
    display: flex; align-items: center; justify-content: center;
    text-align: center;
    font-family: "Libre Baskerville", serif;
    font-weight: 400;
    letter-spacing: 0.12em;
    text-transform: uppercase;
    font-size: 15px;
    line-height: 1.7;
  }
  .card--front .brand-seal {
    left: 68px; top: 62px;
    border: 1.5px solid var(--deep-teal);
    color: var(--deep-teal);
  }
  .card--back .brand-seal {
    left: 210px; top: 73px;
    width: 220px; height: 220px;
    border: 1.5px solid var(--card-white);
    color: var(--card-white);
    font-size: 16px;
  }

  .contact-block { position: absolute; left: 338px; top: 74px; }
  .person-name {
    font-family: "Libre Baskerville", serif;
    font-weight: 700;
    font-size: 26px;
    color: var(--deep-teal);
    letter-spacing: 0.01em;
  }
  .person-role {
    font-size: 14px;
    color: var(--deep-teal);
    margin-top: 2px;
    padding-bottom: 6px;
    width: 64px;
    border-bottom: 1.5px solid var(--rule-grey);
  }
  .contact-list { list-style: none; margin-top: 20px; }
  .contact-list li {
    display: flex; align-items: center;
    font-size: 13.5px;
    color: var(--ink-grey);
    height: 22px;
  }
  .contact-icon {
    width: 16px; height: 16px;
    border-radius: 3px;
    background: var(--deep-teal);
    margin-right: 9px;
    flex: none;
    display: flex; align-items: center; justify-content: center;
  }

  .accent-band { position: absolute; left: 0; top: 0; }
</style>
</head>
<body>

<section class="card card--front" aria-label="Card front">
  <div class="brand-seal">Rosalind<br>Thorpe<br>Gardens</div>

  <div class="contact-block">
    <h1 class="person-name">Corinne Haldwick</h1>
    <p class="person-role">Owner</p>
    <ul class="contact-list">
      <li>
        <span class="contact-icon">
          <svg width="10" height="10" viewBox="0 0 24 24" aria-hidden="true"><path fill="#fff" d="M6.6 10.8a15.1 15.1 0 0 0 6.6 6.6l2.2-2.2c.3-.3.7-.4 1-.2 1.1.4 2.3.6 3.6.6.6 0 1 .4 1 1V20c0 .6-.4 1-1 1A17 17 0 0 1 3 4c0-.6.4-1 1-1h3.5c.6 0 1 .4 1 1 0 1.3.2 2.5.6 3.6.1.3 0 .7-.2 1z"/></svg>
        </span>913-555-0147
      </li>
      <li><span class="contact-icon"></span>Rosalind Thorpe Gardens</li>
      <li><span class="contact-icon"></span>@RosalindThorpeGardens</li>
      <li>
        <span class="contact-icon">
          <svg width="10" height="10" viewBox="0 0 24 24" aria-hidden="true"><g fill="none" stroke="#fff" stroke-width="2"><circle cx="12" cy="12" r="9"/><path d="M3 12h18M12 3c3 3 3 15 0 18M12 3c-3 3-3 15 0 18"/></g></svg>
        </span>RosalindThorpeGardens.example
      </li>
    </ul>
  </div>

  <svg class="accent-band" width="640" height="366" aria-hidden="true">
    <rect x="0" y="318" width="338" height="5" fill="var(--rule-grey)"/>
    <polygon points="352,300 640,300 640,314 344,314" fill="var(--deep-teal)"/>
  </svg>
</section>

<section class="card card--back" aria-label="Card back">
  <div class="brand-seal">Rosalind<br>Thorpe<br>Gardens</div>
</section>

</body>
</html>
```